Panty packaging

what we are looking for is 1 of a kind packaging for women's panties. It should have the same theme for all styles but a different outline or a color code setting the difference between styles. Most company's are packaging in a poly bag or hanger, what we are looking for is a box packaging. also customer should be able to see whats in the box without having to open the box. If there are different colors, the window should show that. We want to be able to customize the design for different styles and for 1 color package or multi color package. It should be sleek and sophisticated. Box does not have to be square, it can have curved edges or be totally round, the most important thins is that it should be stack-able. Sometimes the box will hold a pack of 3 and sometimes a single item, so box height may vary. We need a graphic on the box to indicate the style, for example: hipster, brief, hi cut, or lo cut. box needs a space to put a small size chart. Out logo can be color changed to match theme and background colors, just stick with the 3 colors, black, white, and magneta.
Target Market(s)
Female market all ages. upscale market
Industry/Entity Type
It Company
Look and feel

```html
<!DOCTYPE html>
<html lang="en">
<head>
<meta charset="utf-8">
<title>Panty Box Range – Brief, Hipster, Hi Cut</title>
<link rel="stylesheet" href="https://fonts.googleapis.com/css2?family=Fira+Sans+Extra+Condensed:ital,wght@0,500;0,600;1,600&display=swap">
<style>
  :root {
    --page: #ffffff;
    --tab: #dedede;
    --tab-slot: #ffffff;

    --teal-light: #9eeefa;
    --teal-mid: #2fbccf;
    --teal-dark: #07838f;
    --teal-band: #0f98a8;
    --teal-ink: #bff2f9;

    --pink-light: #f99ee0;
    --pink-mid: #ea4bbd;
    --pink-dark: #b30c82;
    --pink-band: #bf138b;
    --pink-ink: #fcbde9;

    --black-light: #777777;
    --black-mid: #2a2a2a;
    --black-dark: #000000;
    --black-band: #8c8c8c;
    --black-ink: #ececec;
    --badge: #c4c4c4;
  }

  * { box-sizing: border-box; margin: 0; padding: 0; }

  html, body {
    width: 1200px;
    height: 900px;
    overflow: hidden;
    background: var(--page);
  }

  .range {
    width: 1200px;
    height: 900px;
    display: flex;
    justify-content: center;
    align-items: center;
    gap: 40px;
  }

  .box {
    position: relative;
    width: 340px;
    padding-top: 30px;
  }

  .hang-tab {
    position: absolute;
    top: 0;
    left: 50%;
    width: 78px;
    height: 32px;
    margin-left: -39px;
    background: var(--tab);
  }
  .hang-tab::after {
    content: "";
    position: absolute;
    left: 17px;
    top: 10px;
    width: 44px;
    height: 8px;
    border-radius: 4px;
    background: var(--tab-slot);
  }

  .box-front {
    position: relative;
    width: 340px;
    height: 428px;
    overflow: hidden;
    font-family: "Fira Sans Extra Condensed", "Arial Narrow", sans-serif;
    font-weight: 600;
    text-transform: uppercase;
  }

  .box--brief  .box-front { background: linear-gradient(150deg, var(--teal-light) 0%, var(--teal-mid) 45%, var(--teal-dark) 100%); }
  .box--hipster .box-front { background: linear-gradient(170deg, var(--pink-light) 0%, var(--pink-mid) 50%, var(--pink-dark) 100%); }
  .box--hicut  .box-front { background: linear-gradient(180deg, var(--black-light) 0%, var(--black-mid) 55%, var(--black-dark) 100%); }

  .brand-band {
    position: absolute;
    top: 26px;
    left: 0;
    width: 300px;
    height: 72px;
    display: flex;
    align-items: center;
    padding-left: 14px;
    font-size: 50px;
    letter-spacing: 0.5px;
    line-height: 1;
  }

  .style-band {
    position: absolute;
    top: 178px;
    left: 0;
    height: 43px;
    padding: 0 14px;
    display: flex;
    align-items: center;
    font-size: 33px;
    line-height: 1;
  }

  .size-band {
    position: absolute;
    top: 228px;
    left: 0;
    width: 44px;
    height: 26px;
    padding-left: 14px;
    display: flex;
    align-items: center;
    font-size: 20px;
    font-weight: 500;
    line-height: 1;
  }

  .box--brief .brand-band, .box--brief .style-band, .box--brief .size-band { background: var(--teal-band); color: var(--teal-ink); }
  .box--hipster .brand-band, .box--hipster .style-band, .box--hipster .size-band { background: var(--pink-band); color: var(--pink-ink); }
  .box--hicut .brand-band, .box--hicut .style-band { background: var(--black-band); color: var(--black-ink); }

  .pack-badge {
    position: absolute;
    top: 97px;
    left: 210px;
    width: 52px;
    height: 52px;
    border-radius: 50%;
    background: var(--badge);
    border: 2px solid #e6e6e6;
    color: #ffffff;
    display: flex;
    align-items: center;
    justify-content: center;
    font-size: 24px;
    font-style: italic;
    text-transform: none;
  }

  .product-window {
    position: absolute;
    inset: 0;
    width: 340px;
    height: 428px;
  }
</style>
</head>
<body>
  <main class="range">

    <article class="box box--brief">
      <div class="hang-tab"></div>
      <div class="box-front">
        <div class="brand-band">Lorem Ipsum</div>
        <div class="style-band">Brief</div>
        <div class="size-band">M</div>
        <svg class="product-window" viewBox="0 0 340 428" aria-hidden="true">
          <defs>
            <linearGradient id="window-brief" x1="0" y1="0" x2="0" y2="1">
              <stop offset="0" stop-color="#c9f5fb" stop-opacity="0.55"/>
              <stop offset="1" stop-color="#7fd3df" stop-opacity="0.55"/>
            </linearGradient>
          </defs>
          <path d="M44 394 C150 372 238 330 252 250 C264 170 280 126 301 119 L301 394 Z"
                fill="url(#window-brief)" stroke="#077a86" stroke-width="1.5"/>
        </svg>
      </div>
    </article>

    <article class="box box--hipster">
      <div class="hang-tab"></div>
      <div class="box-front">
        <div class="brand-band">Lorem Ipsum</div>
        <div class="style-band">Hipster</div>
        <div class="size-band">S</div>
        <svg class="product-window" viewBox="0 0 340 428" aria-hidden="true">
          <defs>
            <linearGradient id="window-hipster" x1="0" y1="0" x2="0" y2="1">
              <stop offset="0" stop-color="#f6d2ec" stop-opacity="0.75"/>
              <stop offset="0.6" stop-color="#c97bb2" stop-opacity="0.7"/>
              <stop offset="1" stop-color="#e6a6d3" stop-opacity="0.75"/>
            </linearGradient>
          </defs>
          <path d="M44 394 C150 372 238 330 252 250 C264 170 280 126 301 119 L301 394 Z"
                fill="url(#window-hipster)" stroke="#9c0f72" stroke-width="1.5"/>
        </svg>
      </div>
    </article>

    <article class="box box--hicut">
      <div class="hang-tab"></div>
      <div class="box-front">
        <div class="brand-band">Lorem Ipsum</div>
        <div class="style-band">Hi Cut</div>
        <div class="pack-badge">x2</div>
        <svg class="product-window" viewBox="0 0 340 428" aria-hidden="true">
          <defs>
            <linearGradient id="window-hicut" x1="0" y1="0" x2="0" y2="1">
              <stop offset="0" stop-color="#8e8e8e" stop-opacity="0.8"/>
              <stop offset="0.5" stop-color="#d0d0d0" stop-opacity="0.75"/>
              <stop offset="1" stop-color="#7a7a7a" stop-opacity="0.8"/>
            </linearGradient>
          </defs>
          <path d="M44 394 C150 372 238 330 252 250 C264 170 280 126 301 119 L301 394 Z"
                fill="url(#window-hicut)" stroke="#bdbdbd" stroke-width="1.5"/>
        </svg>
      </div>
    </article>

  </main>
</body>
</html>
```